Redesign two existing website pages and one new landing page for dental office

I need to redesign two webpages on my dental website, the Home page (http://velbridgedental.com) and the Dental Implant Services page (http://www.velbridgedental.com/dental-implant-services) and also create a landing page for the Dental Implant Services page.

Please use the same color scheme, slogans and subtitles for the redesign pages and create a reserved video spot on each page. The video spots should not be too big but not too small either and positioned in a central key location on each of the pages. The final redesigned pages should communicate leadership, confidence and trust.

The new landing page for the Dental implant Services page must not have any hyperlinks on the page and must entice the viewer to give name and email before downloading a "Free" eBook called "Is a Fuller Smile Worth the Wait?" Any added photo images to this new page must be smiling.
Updates

Project Deadline Extended Reason: I got feedback that my project was not long enough so I'm extending it by 5 days. Added Thursday, April 16, 2015

Target Market(s)

People who are middle-age to seniors.

Industry/Entity Type

Dental

Coding

Coded - Design and coding required

Number of Pages Required

3 page

Requirements
Must have
• Compatible with existing website colors and theme.

```html
<!DOCTYPE html>
<html lang="en">
<head>
<meta charset="utf-8">
<title>Dental Services</title>
<link href="https://fonts.googleapis.com/css2?family=Open+Sans:wght@300;400;600;700&display=swap" rel="stylesheet">
<style>
  :root {
    --teal: #2f6565;
    --heading-gray: #5a5a5a;
    --body-text: #3e5656;
    --band-gray: #b8b9bb;
    --button-text: #ffffff;
    --band-button-text: #e4e6e6;
    --page-bg: #ffffff;
    --arc-gray: #e3e3e3;
  }
  * { margin: 0; padding: 0; box-sizing: border-box; }
  html, body { width: 1200px; height: 900px; overflow: hidden; background: var(--page-bg); }
  body { position: relative; font-family: "Open Sans", Arial, sans-serif; color: var(--body-text); }

  .service-title { position: absolute; font-size: 28px; font-weight: 600; color: var(--heading-gray); line-height: 1; white-space: nowrap; }
  .service-subtitle { position: absolute; font-size: 19.5px; font-weight: 300; color: var(--teal); line-height: 1; white-space: nowrap; }
  .photo { position: absolute; }
  .service-text { position: absolute; font-size: 15.5px; font-weight: 300; line-height: 23px; color: var(--body-text); }
  .learn-button { position: absolute; width: 133px; height: 45px; background: var(--teal); color: var(--button-text); font-size: 16px; font-weight: 600; display: flex; align-items: center; justify-content: center; border-radius: 2px; }
  .remember-title { position: absolute; font-size: 15px; font-weight: 400; color: var(--teal); }
  .remember-list { position: absolute; list-style: none; font-size: 12.5px; font-weight: 400; line-height: 17.5px; color: var(--teal); }
  .remember-list li { padding-left: 12px; text-indent: -12px; }

  .promo-headline { position: absolute; left: 906px; top: 30px; font-size: 46px; font-weight: 600; color: var(--teal); line-height: 1.1; white-space: nowrap; }
  .promo-subline { position: absolute; left: 906px; top: 88px; font-size: 44px; font-weight: 300; color: var(--teal); line-height: 1.1; white-space: nowrap; }
  .promo-text { position: absolute; font-size: 14.5px; font-weight: 300; line-height: 21px; color: var(--body-text); }
  .promo-request { position: absolute; left: 891px; top: 469px; font-size: 15.5px; font-weight: 600; color: var(--teal); }

  .cta-band { position: absolute; left: 43px; top: 666px; width: 1106px; height: 178px; background: var(--band-gray); border-radius: 10px; text-align: center; }
  .cta-tagline { position: absolute; left: 0; right: 0; top: 28px; font-size: 27px; font-weight: 400; color: var(--teal); }
  .cta-button { position: absolute; left: 344px; top: 76px; width: 463px; height: 65px; background: var(--teal); color: var(--band-button-text); font-size: 33px; font-weight: 400; display: flex; align-items: center; justify-content: center; }

  .footer-arcs { position: absolute; left: 0; top: 885px; }
</style>
</head>
<body>
  <!-- Hygiene column -->
  <h2 class="service-title" style="left:49px;top:35px;">Dental Hygiene Services</h2>
  <p class="service-subtitle" style="left:52px;top:73px;">Achieve Better Health With Prevention</p>
  <div class="photo" role="img" aria-label="Dental floss container and toothbrush with toothpaste on a light surface"
       style="left:58px;top:111px;width:323px;height:211px;background:linear-gradient(135deg,#e9eeee 0%,#dfe7e6 55%,#cfdcdb 100%);border:1px solid #d7dede;"></div>
  <p class="service-text" style="left:62px;top:343px;width:330px;">Maintain healthy teeth and gums with con-<br>sistent dental exams and teeth cleanings by<br>one of our professional dental hygienists.</p>
  <div class="learn-button" style="left:64px;top:427px;">Learn More</div>
  <h3 class="remember-title" style="left:62px;top:492px;">Remember</h3>
  <ul class="remember-list" style="left:58px;top:517px;width:330px;">
    <li>-&nbsp; Improve your health with consistent dental checkups</li>
    <li>-&nbsp; Save time with convenient appointment options close to home</li>
    <li>-&nbsp; Teach kids to develop good dental habits and to maintain a life time of preventive dental care</li>
  </ul>

  <!-- Emergency column -->
  <h2 class="service-title" style="left:469px;top:35px;">Dental Emergency Services</h2>
  <p class="service-subtitle" style="left:471px;top:73px;">Stop Pain From Tooth Trauma and Infection</p>
  <div class="photo" role="img" aria-label="Woman biting into a green apple"
       style="left:540px;top:120px;width:275px;height:212px;background:linear-gradient(90deg,#ffffff 0%,#eef3df 20%,#f1d9c8 55%,#e9c7b0 100%);"></div>
  <p class="service-text" style="left:477px;top:343px;width:350px;">Dental emergencies can and will happen<br>suddenly.&nbsp; Treat all tooth infections and dental<br>trauma (without delay) whenever they occur.</p>
  <div class="learn-button" style="left:479px;top:427px;">Learn More</div>
  <h3 class="remember-title" style="left:476px;top:492px;">Remember</h3>
  <ul class="remember-list" style="left:472px;top:517px;width:330px;">
    <li>-&nbsp; Improve your health with consistent dental checkups</li>
    <li>-&nbsp; Save time with convenient appointment options close to home</li>
    <li>-&nbsp; Teach kids to develop good dental habits and to maintain a life time of preventive dental care</li>
  </ul>

  <!-- Promo column -->
  <h2 class="promo-headline">Don't Wait</h2>
  <p class="promo-subline">'til it Hurts!</p>
  <div class="photo" role="img" aria-label="Woman holding her cheek with tooth pain"
       style="left:894px;top:153px;width:261px;height:237px;background:linear-gradient(135deg,#d9c7bd 0%,#e8d3c6 45%,#cfae9c 100%);"></div>
  <p class="promo-text" style="left:888px;top:412px;width:290px;">Get acquanted today with comfortable<br>dental care.</p>
  <h3 class="promo-request">Request an Appointment</h3>
  <p class="promo-text" style="left:892px;top:501px;width:280px;">We will contact you right away to<br>schedule your dental appointment.</p>

  <!-- Call to action band -->
  <section class="cta-band">
    <p class="cta-tagline">Comprehensive Family Dentistry in One Sugar Land Dental Office!</p>
    <div class="cta-button">Schedule An Appointment</div>
  </section>

  <svg class="footer-arcs" width="1200" height="15" viewBox="0 0 1200 15" aria-hidden="true">
    <g fill="none" stroke="var(--arc-gray)" stroke-width="3">
      <path d="M100 15 Q150 8 200 15"/>
      <path d="M380 15 Q430 8 480 15"/>
      <path d="M660 15 Q710 8 760 15"/>
      <path d="M940 15 Q990 8 1040 15"/>
    </g>
  </svg>
</body>
</html>
```